Website redesign for Halt and Fullmane

We would like to update the design of our current website to a more concise, conversion optimized design.
The goal of our website is to get our message across as concisely as possible plus encourage people to contact us for more information or to book a consultation.
We need a redesign of the home page and 1 internal page - just for design/layout purposes/format purposes.

Target Market(s)

Males 20-45 years old who are concerned about hair loss and who want to regrow their own hair.

Industry/Entity Type

Health And Wellness

Number of Pages Required

2 page

Font styles to use
Sans Serif

Colors
00a990
33a6d7
ffffff
9d9d9d

Requirements
Must have
• We want the home page to be very concise and to the point in getting the message across. We want to get across the following 6 key messages:
• 1. Dr Pembrook story – why he created this solution
• 2. Hair loss is caused by a chemical imbalance
• 3. Halt and fullmane conducts genetic and DNA analysis, then rebalances body chemistry, thus reversing the hair loss process and enabling your own hair to regrow naturally
• 4. Money back guaranteed results
• 5. Purely Core ingredients – no harsh preservatives or chemicals are included
• 6. All ingredients are FDA approved and safe – no side effects
• We also need a strong call to action. We want people to call or email us to find out more information or to schedule a consultation.
• Here is our current website which is not performing as we would hope: http://www.haltandfullmane.example/
• Here is our press release for further information: https://www.pressdeskhub.example/news/finally-we-now-have-a-cure-for-male-pattern-baldness-28461902
• I uploaded the logo files, but let me know if anything else is needed and I can add it.

```html
<!DOCTYPE html>
<html lang="en">
<head>
<meta charset="utf-8">
<title>Halt and Fullmane — Home</title>
<link href="https://fonts.googleapis.com/css2?family=Open+Sans:wght@400;600;700&display=swap" rel="stylesheet">
<style>
:root{
  --teal:#16a596;
  --band:#1e8c96;
  --blue:#33a6d7;
  --grey:#9d9d9d;
  --panel:#f1f1f1;
  --text:#555;
  --dark:#333333;
  --darker:#2a2a2a;
  --white:#ffffff;
}
*{box-sizing:border-box;margin:0;padding:0}
html,body{width:1200px;height:3586px;overflow:hidden}
body{font-family:"Open Sans",Arial,sans-serif;color:var(--text);background:var(--white)}
.wrap{width:938px;margin:0 auto;position:relative}
/* header */
.site-header{height:115px}
.site-header .wrap{height:115px;display:flex;align-items:center;justify-content:space-between}
.brand{display:flex;align-items:center;gap:14px}
.brand-dot{width:34px;height:34px;border-radius:50%;background:var(--teal)}
.brand-name{font-size:30px;font-weight:600;color:var(--teal);line-height:1}
.brand-sub{font-size:17px;color:var(--teal);margin-top:6px}
.call{display:flex;align-items:center;gap:12px;text-align:right}
.call small{display:block;font-size:13px;color:#777}
.call strong{font-size:22px;font-weight:400;color:var(--teal)}
/* nav */
.main-nav{height:38px;background:var(--teal)}
.main-nav ul{list-style:none;display:flex;height:38px}
.main-nav li{color:var(--white);font-size:13px;line-height:38px;padding:0 27px}
.main-nav li.active{background:#0f8a7d}
/* hero */
.hero{height:461px;background:linear-gradient(90deg,#e9eced,#f7f8f8 55%,#eef1f1);position:relative}
.hero-photo{position:absolute;left:240px;top:0;width:380px;height:461px;background:linear-gradient(180deg,#cfc6bd,#b59c86 55%,#e2dcd6)}
.hero-copy{position:absolute;right:134px;top:100px;text-align:right;width:460px}
.hero-copy h1{font-size:26px;font-weight:400;color:#333;line-height:1.3}
.hero-copy .guarantee{font-size:24px;font-weight:700;color:var(--teal);margin-top:6px}
.newsletter{margin:22px 0 0 auto;width:363px;height:109px;background:#8f8f8f;color:var(--white);text-align:center;padding-top:26px}
.newsletter b{display:block;font-size:22px}
.newsletter span{font-size:13px}
.slide-arrow{position:absolute;top:215px;width:20px;height:30px}
/* sections */
.section-title{text-align:center;color:var(--blue);font-size:24px;font-weight:400;padding-top:78px;height:129px}
.split{display:flex;height:400px}
.split .col{width:50%;position:relative}
.text-col{background:var(--panel);padding:34px 28px;font-size:12px;line-height:1.75;color:#666}
.text-col p+p{margin-top:14px}
.btn-ghost{display:inline-block;margin-top:24px;border:1px solid #ccc;background:var(--white);padding:9px 20px;font-size:12px;color:#777}
.photo{background:linear-gradient(135deg,#d9d3cd,#b9a999 60%,#e6e1dc)}
.blue-panel{background:var(--blue);color:var(--white);text-align:center}
.blue-panel b{display:block;font-size:26px;font-weight:700}
.btn-light{display:inline-block;border:1px solid rgba(255,255,255,.8);padding:8px 18px;font-size:13px;margin-top:10px}
.band{background:var(--band);color:var(--white);text-align:center;height:201px;display:flex;flex-direction:column;justify-content:center;align-items:center}
.band p{font-size:24px;line-height:1.5}
.btn-white{background:var(--white);color:#333;font-size:13px;padding:12px 20px;margin-top:20px;border-radius:2px}
/* how it works */
.how .tile{position:relative;color:var(--white);font-weight:700;font-size:17px;text-align:center;text-transform:uppercase}
.tile span{position:absolute;left:0;right:0;bottom:18px;line-height:1.3}
.note{text-align:center;font-size:12px;font-style:italic;color:#666;width:900px;margin:32px auto 0;line-height:1.6}
.more{display:block;text-align:center;color:var(--blue);font-size:13px;text-decoration:underline;margin-top:10px}
/* footer */
.site-footer{background:var(--dark);height:203px;color:#ccc}
.site-footer .wrap{display:flex;padding-top:34px}
.site-footer h4{font-size:16px;font-weight:400;color:var(--white);margin-bottom:10px}
.site-footer ul{list-style:none;font-size:10px;line-height:1.9}
.copy{background:var(--darker);height:77px;text-align:center;font-size:10px;color:#aaa;line-height:77px}
.social{display:grid;grid-template-columns:repeat(3,24px);gap:10px}
.social i{display:block;width:24px;height:24px;border-radius:50%;background:#666}
</style>
</head>
<body>
<header class="site-header">
  <div class="wrap">
    <div class="brand">
      <div class="brand-dot"></div>
      <div>
        <div class="brand-name">Halt &amp; Fullmane</div>
        <div class="brand-sub">by Alan Pembrook M.D.</div>
      </div>
    </div>
    <div class="call">
      <div><small>Call us on</small><strong>(310) 555-0147</strong></div>
      <svg width="16" height="34" viewBox="0 0 16 34"><rect x="1" y="1" width="14" height="32" rx="3" fill="none" stroke="#333" stroke-width="2"/><circle cx="8" cy="28" r="1.6" fill="#333"/></svg>
    </div>
  </div>
</header>
<nav class="main-nav">
  <ul class="wrap">
    <li class="active">Home</li><li>About Us</li><li>How it Works</li><li>Success Stories</li><li>FAQs</li><li>Blog</li><li>Salon Partners</li><li>Book Now</li><li>Contact</li>
  </ul>
</nav>
<section class="hero">
  <div class="hero-photo" role="img" aria-label="Young man with a towel checking his hairline"></div>
  <svg class="slide-arrow" style="left:24px" viewBox="0 0 20 30"><path d="M15 3 4 15l11 12" fill="none" stroke="#333" stroke-width="3"/></svg>
  <svg class="slide-arrow" style="right:24px" viewBox="0 0 20 30"><path d="M5 3l11 12L5 27" fill="none" stroke="#333" stroke-width="3"/></svg>
  <div class="hero-copy">
    <h1>The First Non-Surgical Hair<br>Loss Solution With Clinically<br>Proven Results</h1>
    <div class="guarantee">100% MONEY BACK GUARANTEE! *</div>
    <div class="newsletter"><b>SIGN UP FOR OUR NEWSLETTER</b><span>Receive Free Hair Regrowth Advice &amp; Special Offers</span></div>
  </div>
</section>

<h2 class="section-title">Why Dr Pembrook created this solution</h2>
<div class="wrap split">
  <div class="col text-col">
    <p>Dr. Alan Pembrook, the creator of Halt and Fullmane is a renowned hair restoration expert. After seeing first his father and then older brothers thin and go bald, he dedicated his life to finding the cure for hair loss. After initially pioneering the single hair method for hair transplant, he determined there must be a non-surgical solution and spent the last 20 years in research and clinical trial and error first creating, then perfecting what is now the Halt and Fullmane solution for hair loss.</p>
    <p>To the right you can see the Pembrook family tree, or at least the five Pembrook brothers from oldest to youngest. Unluckily for the oldest three Dr Pembrook did not discover the cure until it was too late for them. As you can see both Alan and his younger brother (Alan is the second youngest) sport a full head of hair despite both now being well beyond the age when their older brothers had already lost their hair.</p>
    <span class="btn-ghost">Read more</span>
  </div>
  <div class="col">
    <div class="photo" style="height:261px" role="img" aria-label="Man examining his receding hairline"></div>
    <div class="blue-panel" style="height:139px;padding-top:20px">
      <b>HALT AND FULLMANE</b>
      <div style="font-size:17px">See Your Future, Change Your Future</div>
      <span class="btn-light">&#9654; Play Video</span>
    </div>
  </div>
</div>
<div style="height:86px"></div>
<section class="band">
  <p>The Revolutionary New Solution For Hair Loss That Uses Personalized Medicine<br>To Stop Hair Loss and Regrow Your Thinning / Receding Hair.</p>
  <span class="btn-white">Learn More</span>
</section>

<h2 class="section-title">Hair loss is caused by a chemical imbalance</h2>
<div class="wrap split" style="height:401px">
  <div class="col">
    <div class="photo" style="height:233px;background:linear-gradient(135deg,#f0ece8,#d8c7b2 55%,#eeeae6)" role="img" aria-label="Woman looking at thinning hair"></div>
    <svg style="position:absolute;left:195px;top:205px" width="76" height="44" viewBox="0 0 76 44"><rect width="76" height="44" rx="3" fill="#444"/></svg>
    <div class="blue-panel" style="height:168px;padding-top:38px">
      <div style="font-size:17px">All ingredients are</div>
      <b>FDA APPROVED AND SAFE</b>
      <span class="btn-light">&#10003; No Side Effects</span>
    </div>
  </div>
  <div class="col text-col" style="background:var(--panel)">
    <p>Hair loss often begins when hormones and nutrients fall out of balance. Your follicles respond by shrinking, growth cycles shorten, and strands thin over time. Our team measures the markers that drive this change so treatment can target the true cause rather than the symptoms.</p>
    <p>Using your genetic profile, we build a formula suited to your body. It restores balance gently and steadily, allowing dormant follicles to return to a healthy growth phase. Most clients notice less shedding within the first months, followed by thicker and fuller growth as the balance holds. Every plan is reviewed by our doctors along the way.</p>
    <span class="btn-ghost">Read more</span>
  </div>
</div>
<div style="height:79px"></div>
<section class="band">
  <p>Purely Core ingredients<br>No harsh preservatives or chemicals are included</p>
  <span class="btn-white">Learn More</span>
</section>

<h2 class="section-title" style="height:125px">How It Works</h2>
<div class="wrap how">
  <div class="tile" style="height:278px;background:linear-gradient(135deg,#0b3f7a,#1f7fd0 50%,#0a2f5c)" role="img" aria-label="Blue DNA double helix">
    <span>Halt and Fullmane conducts genetic and DNA analysis</span>
  </div>
  <div style="display:flex;gap:6px;margin-top:7px">
    <div class="tile" style="width:466px;height:282px;background:linear-gradient(135deg,#e8e4e0,#9c8574 55%,#4b3a30)" role="img" aria-label="Woman running hands through her hair">
      <span>Then rebalances body chemistry</span>
    </div>
    <div class="tile" style="width:466px;height:282px;background:linear-gradient(135deg,#6c5a44,#d9b77a 50%,#3a2f24)" role="img" aria-label="Woman with long flowing blonde hair">
      <span>Thus reversing the hair loss process<br>and enabling your own hair<br>to regrow naturally</span>
    </div>
  </div>
</div>
<p class="note">* Note: Individual results may vary. If after 12 months of continued use of the Halt &amp; Fullmane personalized solution as directed, the Halt &amp; Fullmane Solution has not worked to regrow your hair as promised, Dr. Pembrook will offer a full refund of all products purchased.</p>
<span class="more">More Details.</span>
<div style="height:70px"></div>
<section class="band" style="height:198px">
  <p>Stop Hereditary Hair Loss And Regrow a Full,<br>Healthy Head of Hair</p>
  <span class="btn-white">Are You A Candidate?</span>
</section>

<footer class="site-footer">
  <div class="wrap">
    <div style="width:259px">
      <h4>Links</h4>
      <div style="display:flex;gap:60px">
        <ul><li>» Home</li><li>» About Us</li><li>» How it Works</li><li>» Success Stories</li><li>» FAQs</li></ul>
        <ul><li>» Blog</li><li>» Salon Partners</li><li>» Book Now</li><li>» Contact</li></ul>
      </div>
    </div>
    <div style="width:341px">
      <h4>Contact Info</h4>
      <ul><li>&#9906;&nbsp; 2210 Linden Ave, Suite 300, Westbrook CA 90000</li><li>&#9742;&nbsp; (310) 555-0147</li><li>&#9993;&nbsp; info@haltandfullmane.example</li></ul>
    </div>
    <div style="width:242px">
      <h4>Hours of Operation</h4>
      <ul><li>Monday - Friday: 9:00am to 5:00pm</li><li>Saturday: 9:00am to 2:00pm</li></ul>
    </div>
    <div>
      <h4>Follow us on</h4>
      <div class="social"><i></i><i></i><i></i><i></i><i></i><i></i></div>
    </div>
  </div>
</footer>
<div class="copy">Copyright © 2017 Halt and Fullmane Hair, LLC. All rights reserved.</div>
</body>
</html>
```